Modern Business Card

Modern professional business card with more than just logo and demographic info. Something memorable.

We are a trendy/modern chiropractic group with an emphasis on neurology, hence the minimalist-type brain logo. We want to convey that modern and technical aspect with professionalism and the elite nature of our practice environment.

```html
<!DOCTYPE html>
<html lang="en">
<head>
<meta charset="utf-8">
<title>Meridian Spine – Business Card</title>
<link rel="stylesheet" href="https://fonts.googleapis.com/css2?family=Roboto:wght@400;500&display=swap">
<style>
  :root {
    --brand-blue: #4a80c4;
    --ink: #111111;
    --text-grey: #6f6f6f;
    --swoosh-grey: #6b6b6b;
    --card-white: #fdfdfd;
    --page-bg: #ffffff;
  }
  * { margin: 0; padding: 0; box-sizing: border-box; }
  html, body {
    width: 1200px; height: 1200px; overflow: hidden;
    background: var(--page-bg);
    font-family: "Roboto", Arial, sans-serif;
  }
  .canvas { position: relative; width: 1200px; height: 1200px; }

  .card { position: absolute; overflow: hidden; }
  .card--front { left: 232px; top: 173px; width: 705px; height: 408px; background: var(--card-white); }
  .card--back { left: 231px; top: 628px; width: 702px; height: 401px; background: var(--brand-blue); }

  .card__waves { position: absolute; left: 0; top: 0; width: 705px; height: 408px; }

  .brand-name {
    position: absolute;
    font-weight: 500;
    letter-spacing: 1px;
    line-height: 1;
    text-transform: uppercase;
  }
  .card--front .brand-name { left: 54px; top: 178px; width: 310px; font-size: 40px; color: var(--ink); }
  .card--back .brand-name { right: 42px; top: 282px; font-size: 38px; color: #ffffff; display: flex; align-items: center; gap: 14px; }
  .brand-mark { width: 14px; height: 14px; background: #ffffff; display: inline-block; }

  .divider { position: absolute; left: 387px; top: 89px; width: 2px; height: 231px; background: var(--brand-blue); }

  .person { position: absolute; left: 420px; top: 84px; }
  .person__name { font-size: 32px; font-weight: 400; color: var(--brand-blue); line-height: 1.1; }
  .person__role { font-size: 21px; color: var(--text-grey); margin-top: 2px; }

  .address { position: absolute; left: 413px; top: 165px; font-size: 19px; color: var(--text-grey); line-height: 23px; }

  .contacts { position: absolute; left: 413px; top: 222px; list-style: none; }
  .contacts li { display: flex; align-items: center; height: 26px; font-size: 19px; color: var(--text-grey); }
  .contacts svg { width: 20px; height: 20px; margin-right: 15px; fill: var(--brand-blue); }
</style>
</head>
<body>
<main class="canvas">

  <section class="card card--front" aria-label="Business card front">
    <svg class="card__waves" viewBox="0 0 705 408" aria-hidden="true">
      <path d="M0 338 Q300 392 625 349 Q300 378 0 352 Z" fill="var(--swoosh-grey)"/>
      <path d="M0 362 Q330 410 705 327 L705 408 L0 408 Z" fill="var(--brand-blue)"/>
    </svg>

    <div class="brand-name">Meridian Spine</div>

    <div class="divider"></div>

    <div class="person">
      <div class="person__name">Calder Rowe</div>
      <div class="person__role">President</div>
    </div>

    <address class="address" style="font-style:normal">
      012 Physical Address 000<br>United State 5551
    </address>

    <ul class="contacts">
      <li>
        <svg viewBox="0 0 20 20" aria-hidden="true"><path d="M4 2 L7.5 2 L9 6 L7 7.5 Q8.5 11 12.5 13 L14 11 L18 12.5 L18 16 Q17 18 14.5 17.8 Q5 16 2.2 5.5 Q2 3 4 2 Z"/></svg>
        012 3456 7890
      </li>
      <li>
        <svg viewBox="0 0 20 20" aria-hidden="true"><rect x="5" y="2" width="10" height="5"/><rect x="2" y="8" width="16" height="7" rx="1.5"/><rect x="5" y="13" width="10" height="5" fill="#fff" stroke="var(--brand-blue)" stroke-width="1.5"/></svg>
        00000000051
      </li>
      <li>
        <svg viewBox="0 0 20 20" aria-hidden="true"><path d="M1 4 H17 V10 H12 V15 H1 Z"/><path d="M1.5 4.5 L9 10 L16.5 4.5" stroke="#fff" stroke-width="1.3" fill="none"/><circle cx="15.5" cy="15" r="4"/><path d="M13.5 15 L15 16.5 L17.5 13.5" stroke="#fff" stroke-width="1.3" fill="none"/></svg>
        info@yourmail.com
      </li>
      <li>
        <svg viewBox="0 0 20 20" aria-hidden="true" fill="none"><g stroke="var(--brand-blue)" stroke-width="1.4" fill="none"><circle cx="10" cy="10" r="8"/><ellipse cx="10" cy="10" rx="3.5" ry="8"/><path d="M2 10 H18 M3.5 6 H16.5 M3.5 14 H16.5"/></g></svg>
        www.yourwebside.com
      </li>
    </ul>
  </section>

  <section class="card card--back" aria-label="Business card back">
    <div class="brand-name"><span class="brand-mark"></span>Meridian Spine</div>
  </section>

</main>
</body>
</html>
```